Harborview Estates Business Card for Apartment Buildings

Create business cards for resident managers who run apartment buildings. The audience is the public who are searching for apartment rentals, and current residents who live at the apartment building. Key design element will be incorporating the company logo, however, the logo cannot dominate. The building name and manager name are more important than the logo. Current business card design leaves little room for copy, so we may need to reduce the size on the current card to allow for more space for copy.

Target Market(s)

Adults 18-65 years of age, who are looking for an apartment rental, plus current residents who live at our apartment buildings.

Industry/Entity Type

Property Management

Contact Information for Business Card

A major design element will be use of the company logo. Important property and manager contact information must be part of the design. The size of the logo will need to be reduced to make room for building and manager contact copy.

Font styles to use
Sans Serif

Colors
3176b5
000000
959595
ffffff

Requirements
Must have
• 1) Incorporate the company logo.
• 2) Use the company colors (dark blue, black/grey, over white).
• 3) FEATURE THE BUILDING NAME
• 4) FEATURE THE MANAGER NAME
• 5) The company name is less important than BUILDING and MANAGER
• 6) Manager contact information
• **SEE ATTACHED CREATIVE BRIEF**
Nice to have
• 1) Back of card logo watermark
• 2) Ability to write notes on back of carfd
Should not have
• Avoid letting the company logo dominate the card, the building name and manager are more important than the company logo.

```html
<!DOCTYPE html>
<html lang="en">
<head>
<meta charset="utf-8">
<title>Harborview Estates – Resident Manager Business Card</title>
<link rel="stylesheet" href="https://fonts.googleapis.com/css2?family=Roboto:wght@400;500;700&family=Roboto+Condensed:wght@500;700&display=swap">
<style>
  :root {
    --brand-blue: #0f6aa6;
    --ink-grey: #4a4a4a;
    --soft-grey: #959595;
    --paper: #f4f4f4;
    --backdrop: #2b2b2b;
    --white: #ffffff;
  }
  * { margin: 0; padding: 0; box-sizing: border-box; }
  html, body { width: 1200px; height: 960px; overflow: hidden; }
  body {
    background: var(--backdrop);
    font-family: "Roboto", Arial, sans-serif;
    position: relative;
  }
  .card {
    position: absolute;
    width: 600px;
    height: 343px;
    background: var(--paper);
    overflow: hidden;
  }
  .card--front { left: 314px; top: 113px; }
  .card--back  { left: 311px; top: 472px; }

  .property {
    position: absolute;
    left: 43px;
    top: 28px;
    color: var(--ink-grey);
    font-size: 14px;
    line-height: 19px;
  }
  .property__name {
    font-family: "Roboto", Arial, sans-serif;
    font-weight: 700;
    font-size: 21px;
    line-height: 26px;
    color: var(--brand-blue);
  }
  .property__web { margin-top: 4px; }

  .manager-band {
    position: absolute;
    left: 0;
    top: 130px;
    width: 326px;
    height: 82px;
    background: var(--brand-blue);
    color: var(--white);
    padding: 17px 0 0 43px;
  }
  .manager-band__name {
    font-family: "Roboto Condensed", Arial, sans-serif;
    font-weight: 700;
    font-size: 22px;
    line-height: 26px;
  }
  .manager-band__title {
    font-family: "Roboto", Arial, sans-serif;
    font-weight: 500;
    font-size: 14px;
    line-height: 18px;
  }

  .company-mark {
    position: absolute;
    display: flex;
    align-items: center;
    gap: 10px;
  }
  .company-mark__square {
    width: 40px;
    height: 40px;
    background: var(--brand-blue);
    flex: none;
  }
  .company-mark__name {
    font-family: "Roboto", Arial, sans-serif;
    font-weight: 700;
    color: var(--brand-blue);
    text-transform: uppercase;
    line-height: 1.02;
  }
  .card--front .company-mark { left: 336px; top: 146px; }
  .card--front .company-mark__name { font-size: 24px; }
  .card--back .company-mark { left: 127px; top: 121px; gap: 14px; }
  .card--back .company-mark__square { width: 64px; height: 64px; }
  .card--back .company-mark__name { font-size: 36px; }

  .contact-list {
    position: absolute;
    left: 43px;
    top: 237px;
    list-style: none;
    color: var(--ink-grey);
    font-size: 14px;
  }
  .contact-list li {
    display: flex;
    align-items: center;
    height: 19.3px;
  }
  .contact-list svg {
    width: 13px;
    height: 13px;
    margin-right: 10px;
    fill: var(--brand-blue);
    flex: none;
  }
</style>
</head>
<body>

<section class="card card--front" aria-label="Business card front">
  <div class="property">
    <h1 class="property__name">Cedar Court Apartments</h1>
    <p class="property__street">1842 Linden Avenue</p>
    <p class="property__city">Oakridge, CA 90210</p>
    <p class="property__web">www.harborviewest.com</p>
  </div>

  <div class="manager-band">
    <h2 class="manager-band__name">Marisol Vega</h2>
    <p class="manager-band__title">Resident Manager</p>
  </div>

  <div class="company-mark">
    <span class="company-mark__square"></span>
    <span class="company-mark__name">Harborview<br>Estates</span>
  </div>

  <ul class="contact-list">
    <li>
      <svg viewBox="0 0 16 16" aria-hidden="true"><path d="M3.5 1l2.6 3.2-1.5 1.6c.9 2 2.6 3.7 4.6 4.6l1.6-1.5L14 11.5 12.6 14C6.5 14 2 9.5 2 3.4z"/></svg>
      <span>555-201-4830</span>
    </li>
    <li>
      <svg viewBox="0 0 16 16" aria-hidden="true"><path d="M4.5 0h7A1.5 1.5 0 0 1 13 1.5v13a1.5 1.5 0 0 1-1.5 1.5h-7A1.5 1.5 0 0 1 3 14.5v-13A1.5 1.5 0 0 1 4.5 0zM5 2v10h6V2zm3 11a1 1 0 1 0 0 2 1 1 0 0 0 0-2z"/></svg>
      <span>555-386-7142</span>
    </li>
    <li>
      <svg viewBox="0 0 16 16" aria-hidden="true"><path d="M4 1h8v4H4zM1 6h14v7h-2v-3H3v3H1zm3 5h8v4H4z"/></svg>
      <span>555-640-9215</span>
    </li>
    <li>
      <svg viewBox="0 0 16 16" aria-hidden="true"><path d="M1 3h14v1.2L8 9 1 4.2zm0 2.6l7 4.8 7-4.8V13H1z"/></svg>
      <span>marisol@harborviewest.com</span>
    </li>
  </ul>
</section>

<section class="card card--back" aria-label="Business card back">
  <div class="company-mark">
    <span class="company-mark__square"></span>
    <span class="company-mark__name">Harborview<br>Estates</span>
  </div>
</section>

</body>
</html>
```